New Business Card Design Project

Need a design that will create an impact / strong impression towards our clients for our business. We are in the lighting business and we do lighting retrofits for large commercial to industrial clientele.

Target Market(s)

Lighting Industry

Industry/Entity Type

Business

Font styles to use
Other font styles liked:
• we would like to use the font on our logo, not sure what it is though..

Requirements
Must have
• Our logo.
Nice to have
• We are open to suggestions that have to do with lighting.

```html
<!DOCTYPE html>
<html lang="en">
<head>
<meta charset="utf-8">
<title>Lumenway Retrofit Group – Business Card</title>
<link href="https://fonts.googleapis.com/css2?family=Open+Sans:wght@400;600;700&display=swap" rel="stylesheet">
<style>
  :root {
    --backdrop: #3a3a3a;
    --card-black: #000000;
    --card-white: #ffffff;
    --brand-green: #1f8a3c;
    --text-grey: #555555;
    --logo-white: #ffffff;
    --shadow: rgba(0,0,0,0.45);
  }
  * { margin: 0; padding: 0; box-sizing: border-box; }
  html, body {
    width: 1200px; height: 864px; overflow: hidden;
    background: var(--backdrop);
    font-family: "Open Sans", Arial, sans-serif;
  }
  .stage {
    position: relative; width: 1200px; height: 864px;
    display: flex; flex-direction: column; align-items: center; justify-content: center; gap: 44px;
  }
  .card {
    width: 640px; height: 366px; position: relative;
    box-shadow: 0 10px 30px var(--shadow);
  }
  .card--front { background: var(--card-black); display: flex; align-items: center; justify-content: center; }
  .card--back { background: var(--card-white); display: flex; align-items: center; }

  .brand-name {
    font-weight: 700; font-size: 30px; letter-spacing: 0.5px;
    display: flex; align-items: center; gap: 14px;
  }
  .brand-mark { width: 22px; height: 22px; display: inline-block; }
  .card--front .brand-name { color: var(--logo-white); }
  .card--front .brand-mark { background: var(--brand-green); }
  .card--back .brand-name { color: var(--brand-green); font-size: 24px; gap: 10px; }
  .card--back .brand-mark { background: var(--brand-green); width: 18px; height: 18px; }

  .back-logo { width: 330px; display: flex; justify-content: center; }
  .divider { width: 2px; height: 200px; background: var(--brand-green); }
  .contact { padding-left: 26px; color: var(--text-grey); }
  .contact__name { color: var(--brand-green); font-weight: 700; font-size: 22px; line-height: 1.1; }
  .contact__title { font-size: 15px; margin-bottom: 16px; }
  .contact__address { font-size: 15px; line-height: 1.35; margin-bottom: 14px; }
  .contact__list { list-style: none; font-size: 15px; line-height: 1.45; }
  .contact__list li { display: flex; align-items: center; gap: 8px; padding-left: 16px; }
  .contact__list svg { width: 12px; height: 12px; fill: var(--brand-green); stroke: var(--brand-green); flex: none; }
</style>
</head>
<body>
<main class="stage">
  <section class="card card--front">
    <div class="brand-name"><span class="brand-mark"></span>Lumenway Retrofit Group</div>
  </section>

  <section class="card card--back">
    <div class="back-logo">
      <div class="brand-name"><span class="brand-mark"></span>Lumenway Retrofit Group</div>
    </div>
    <div class="divider"></div>
    <div class="contact">
      <p class="contact__name">John Smith</p>
      <p class="contact__title">President</p>
      <p class="contact__address">Street Name Ave, Suite 100<br>State, Zip Code, Country</p>
      <ul class="contact__list">
        <li><svg viewBox="0 0 12 12"><path stroke="none" d="M2.5 0.5l2 2.5-1.2 1.3c.8 1.6 2 2.8 3.6 3.6L8.2 6.7l2.6 2-.9 2.4C5.2 11.4.6 6.8.9 2z"/></svg>01 012-345-6789</li>
        <li><svg viewBox="0 0 12 12"><rect x="3" y="0.8" width="6" height="10.4" rx="1" fill="none" stroke-width="1.3"/><circle cx="6" cy="9.3" r="0.7" stroke="none"/></svg>01 012-345-6780</li>
        <li><svg viewBox="0 0 12 12"><rect x="0.8" y="2.5" width="10.4" height="7" fill="none" stroke-width="1.2"/><path d="M0.8 2.5L6 6.5l5.2-4" fill="none" stroke-width="1.2"/></svg>info@yourwebsite.com</li>
        <li><svg viewBox="0 0 12 12"><g fill="none" stroke-width="1"><circle cx="6" cy="6" r="5"/><ellipse cx="6" cy="6" rx="2.2" ry="5"/><path d="M1 6h10M2 3.3h8M2 8.7h8"/></g></svg>yourwebsite.com</li>
      </ul>
    </div>
  </section>
</main>
</body>
</html>
```